Bluecrest Learning Corps by graduating students from college in two years

Based on the logo design, create stationary and business cards for
Dr. Venrel T Oskamp, CEO, (703) 482-1736
and Marisa Deltoft, Respresentative, (301) 647-2208
Address: 4719 Pellham Court, Kestrel Falls, OR 97482
Incorporate elelments of the logo

Target Market(s)

USA

Font styles to use
Other font styles liked:
• match with the logo type style

```html
<!DOCTYPE html>
<html lang="en">
<head>
<meta charset="utf-8">
<title>Bluecrest Learning Corps – Business Cards</title>
<link href="https://fonts.googleapis.com/css2?family=Open+Sans:wght@400;700&family=Cinzel:wght@700&display=swap" rel="stylesheet">
<style>
  :root {
    --navy: #13296a;
    --gold: #f6c63c;
    --white: #ffffff;
    --ink-grey: #6b6b6b;
    --rule-grey: #9a9a9a;
    --backdrop: #333333;
  }
  * { box-sizing: border-box; margin: 0; padding: 0; }
  html, body { width: 1200px; height: 780px; overflow: hidden; }
  body {
    background: var(--backdrop);
    font-family: "Open Sans", Arial, sans-serif;
    position: relative;
  }
  .card {
    position: absolute;
    width: 620px;
    height: 354px;
    border-radius: 26px;
    overflow: hidden;
    box-shadow: 0 10px 30px rgba(0,0,0,.45);
  }
  .card-front {
    left: 60px; top: 50px;
    background: var(--navy);
    display: flex; align-items: center; justify-content: center;
  }
  .brand-front { display: flex; align-items: center; gap: 16px; }
  .brand-dot {
    width: 34px; height: 34px; border-radius: 50%;
    background: var(--gold);
    flex: none;
  }
  .brand-name {
    font-family: "Cinzel", Georgia, serif;
    font-weight: 700;
    font-size: 30px;
    letter-spacing: 1px;
    line-height: 1.15;
  }
  .card-front .brand-name { color: var(--white); }
  .card-back {
    left: 520px; top: 376px;
    background: var(--white);
  }
  .back-brand {
    position: absolute;
    left: 34px; top: 0; height: 268px; width: 250px;
    display: flex; align-items: center; gap: 12px;
  }
  .back-brand .brand-dot { width: 26px; height: 26px; }
  .back-brand .brand-name { color: var(--navy); font-size: 22px; }
  .divider {
    position: absolute;
    left: 300px; top: 50px;
    width: 1px; height: 180px;
    background: var(--rule-grey);
  }
  .contacts {
    position: absolute;
    left: 326px; top: 40px;
  }
  .contact + .contact { margin-top: 20px; }
  .contact-name {
    color: var(--navy);
    font-weight: 700;
    font-size: 22px;
    line-height: 1.2;
  }
  .contact-role {
    color: var(--ink-grey);
    font-size: 16px;
    line-height: 1.3;
  }
  .contact-phone {
    color: var(--ink-grey);
    font-size: 16px;
    display: flex; align-items: center; gap: 6px;
    margin-left: 14px;
  }
  .phone-icon { width: 15px; height: 15px; flex: none; }
  .address-band {
    position: absolute;
    left: 0; right: 0; bottom: 0;
    height: 78px;
    background: var(--navy);
    border-top: 5px solid var(--gold);
    display: flex; align-items: center; justify-content: center;
    color: var(--white);
    font-size: 19px;
    letter-spacing: .3px;
  }
</style>
</head>
<body>

<section class="card card-front" aria-label="Business card front">
  <div class="brand-front">
    <span class="brand-dot"></span>
    <span class="brand-name">Bluecrest<br>Learning Corps</span>
  </div>
</section>

<section class="card card-back" aria-label="Business card back">
  <div class="back-brand">
    <span class="brand-dot"></span>
    <span class="brand-name">Bluecrest<br>Learning Corps</span>
  </div>

  <div class="divider"></div>

  <div class="contacts">
    <div class="contact">
      <p class="contact-name">Dr. Venrel T Oskamp</p>
      <p class="contact-role">CEO</p>
      <p class="contact-phone">
        <svg class="phone-icon" viewBox="0 0 24 24" aria-hidden="true"><path fill="#f6c63c" d="M2 9c0-3 5-5 10-5s10 2 10 5v2h-5V8.5c-1.5-.6-3.2-.9-5-.9s-3.5.3-5 .9V11H2zM6 12h12l3 8H3zM12 13.5a3 3 0 1 0 0 6 3 3 0 0 0 0-6z"/></svg>
        (703) 482-1736
      </p>
    </div>
    <div class="contact">
      <p class="contact-name">Marisa Deltoft</p>
      <p class="contact-role">Respresentative</p>
      <p class="contact-phone">
        <svg class="phone-icon" viewBox="0 0 24 24" aria-hidden="true"><path fill="#f6c63c" d="M2 9c0-3 5-5 10-5s10 2 10 5v2h-5V8.5c-1.5-.6-3.2-.9-5-.9s-3.5.3-5 .9V11H2zM6 12h12l3 8H3zM12 13.5a3 3 0 1 0 0 6 3 3 0 0 0 0-6z"/></svg>
        (301) 647-2208
      </p>
    </div>
  </div>

  <div class="address-band">4719 Pellham Court, Kestrel Falls, OR 97482</div>
</section>

</body>
</html>
```